Automotive component supplier needs a business card design

We need a business card design for our company called Velran Global Components Ltd based in the UK. We are a supplier of interior and exterior components to premium car manufacturers such as Corvel Ashby, Hadley Fenn, Marquist and Tavarelli. We would like to see a modern business card design that uses the colour blue.

Target Market(s)

Premium automotive car manufacturers.

Industry/Entity Type

Automotive

Contact Information for Business Card

Company Name : Velran Global Components Limited
Address: 17 Marlow Yard, Upper Heath, Warwick, CV31 8QL, United Kingdom
Web Address : www.velrancomponents-example.co.uk

Font styles to use
Other font styles liked:
• Helvetica

Colors
3176b5
0255a3
85acd3
cfdeed
cee9f5
85cae6
34a6d7
0692cd
9bcb3c

Requirements
Must have
• Clear company logo and a mixture of blue colours.
Nice to have
• A high quality modern image.
Should not have
• Multiple colours.

```html
<!DOCTYPE html>
<html lang="en">
<head>
<meta charset="utf-8">
<title>Velran Global Components – Business Card</title>
<link rel="stylesheet" href="https://fonts.googleapis.com/css2?family=Arimo:wght@400;700&display=swap">
<style>
  :root {
    --backdrop: #2b2c2e;
    --blue: #0692cd;
    --blue-deep: #0255a3;
    --blue-pattern: #34a6d7;
    --green: #9bcb3c;
    --paper: #ffffff;
    --ink-blue: #0a7fc0;
  }
  * { margin: 0; padding: 0; box-sizing: border-box; }
  html, body {
    width: 1200px; height: 900px; overflow: hidden;
    background: var(--backdrop);
    font-family: "Arimo", Helvetica, Arial, sans-serif;
  }
  .canvas { position: relative; width: 1200px; height: 900px; }
  .card {
    position: absolute; width: 620px; height: 354px; overflow: hidden;
    box-shadow: 0 14px 30px rgba(0,0,0,.45);
  }
  .brand { position: absolute; display: flex; align-items: center; gap: 10px; }
  .brand-dot { width: 12px; height: 12px; border-radius: 50%; background: var(--green); flex: none; }
  .brand-name {
    font-weight: 700; letter-spacing: 1px; line-height: 1.1;
  }

  /* Back side */
  .card-back { left: 90px; top: 80px; background: var(--blue); }
  .back-pattern {
    position: absolute; inset: 0;
    background: linear-gradient(135deg, var(--blue) 0%, var(--blue-pattern) 50%, var(--blue) 100%);
    opacity: .9;
  }
  .card-back .brand { right: 44px; bottom: 110px; }
  .card-back .brand-name { color: var(--paper); font-size: 26px; }

  /* Front side */
  .card-front { left: 490px; top: 466px; background: var(--paper); }
  .card-front .brand { left: 34px; top: 100px; }
  .card-front .brand-name { color: var(--ink-blue); font-size: 22px; }
  .wave { position: absolute; inset: 0; }
  .contact {
    position: absolute; right: 28px; top: 36px; text-align: right;
    color: var(--ink-blue); font-size: 13px; line-height: 19px;
  }
  .contact-name {
    font-weight: 700; font-size: 17px; letter-spacing: 2px; line-height: 22px;
  }
  .contact-role { color: var(--green); font-size: 14px; margin-bottom: 4px; }
  .contact-line { display: flex; justify-content: flex-end; align-items: center; gap: 8px; }
  .contact-icon { width: 11px; height: 11px; fill: var(--green); flex: none; }
  .address {
    position: absolute; left: 28px; bottom: 22px;
    color: var(--paper); font-size: 15px; line-height: 20px;
  }
</style>
</head>
<body>
<div class="canvas">

  <section class="card card-back" aria-label="Card back">
    <div class="back-pattern" role="img" aria-label="Repeating brand pattern in blue tones"></div>
    <div class="brand">
      <span class="brand-dot"></span>
      <span class="brand-name">VELRAN GLOBAL<br>COMPONENTS</span>
    </div>
  </section>

  <section class="card card-front" aria-label="Card front">
    <svg class="wave" viewBox="0 0 620 354" preserveAspectRatio="none" aria-hidden="true">
      <path d="M0,292 C150,240 330,250 455,228 C535,214 588,200 620,180 L620,354 L0,354 Z" fill="var(--green)"/>
      <path d="M0,302 C150,252 330,262 460,240 C540,226 590,212 620,194 L620,354 L0,354 Z" fill="var(--blue)"/>
    </svg>

    <div class="brand">
      <span class="brand-dot"></span>
      <span class="brand-name">VELRAN GLOBAL<br>COMPONENTS</span>
    </div>

    <div class="contact">
      <div class="contact-name">DANA WHITLOCK</div>
      <div class="contact-role">Director</div>
      <div class="contact-line">01926 555 014
        <svg class="contact-icon" viewBox="0 0 24 24"><path d="M6.6 10.8a15 15 0 0 0 6.6 6.6l2.2-2.2c.3-.3.7-.4 1-.2 1.1.4 2.3.6 3.6.6.6 0 1 .4 1 1V20c0 .6-.4 1-1 1A17 17 0 0 1 3 4c0-.6.4-1 1-1h3.5c.6 0 1 .4 1 1 0 1.3.2 2.5.6 3.6.1.3 0 .7-.2 1z"/></svg>
      </div>
      <div class="contact-line">07700 900 318
        <svg class="contact-icon" viewBox="0 0 24 24"><path d="M7 1h10a2 2 0 0 1 2 2v18a2 2 0 0 1-2 2H7a2 2 0 0 1-2-2V3a2 2 0 0 1 2-2zm0 3v14h10V4z"/></svg>
      </div>
      <div class="contact-line">hello@velrancomponents-example.co.uk
        <svg class="contact-icon" viewBox="0 0 24 24"><path d="M2 5h20v14H2zm2 2v.5l8 5 8-5V7z"/></svg>
      </div>
      <div class="contact-line">www.velrancomponents-example.co.uk
        <svg class="contact-icon" viewBox="0 0 24 24"><circle cx="12" cy="12" r="10"/></svg>
      </div>
    </div>

    <div class="address">
      17 Marlow Yard, Upper Heath<br>
      Warwick, CV31 8QL, UK
    </div>
  </section>

</div>
</body>
</html>
```